Retractable banner.
Health Check For Pets
Check for Ear Mites
Skin Health
Fleas & Ticks

A space SERVE BY <NAME OF CLINIC>

Ideally contain pictures of cats and dogs

```html
<!DOCTYPE html>
<html lang="en">
<head>
<meta charset="utf-8">
<title>Health Check for Pets – Retractable Banner</title>
<link rel="stylesheet" href="https://fonts.googleapis.com/css2?family=Montserrat:wght@700;800;900&display=swap">
<style>
  :root {
    --red: #c61f2b;
    --white: #ffffff;
    --ink-grey: #555659;
    --ring-grey: #58595b;
    --panel-top: #ffffff;
    --panel-bottom: #c9cacc;
    --bg-glow: #f1f2f3;
    --cat-tone-a: #8a7762;
    --cat-tone-b: #d9d2c6;
    --dog-tone-a: #c98e4e;
    --dog-tone-b: #e0b27a;
    --mite-tone: #efe2a6;
    --pup-tone: #a9c1ea;
    --tick-tone: #9a4f23;
  }
  * { margin: 0; padding: 0; box-sizing: border-box; }
  html, body { width: 1200px; height: 667px; overflow: hidden; background: var(--white); }
  .banner {
    position: relative;
    width: 1200px; height: 667px;
    background: radial-gradient(ellipse at 50% 40%, var(--white) 35%, var(--bg-glow) 100%);
    font-family: "Montserrat", "Arial Black", sans-serif;
    overflow: hidden;
  }
  .headline {
    position: absolute; left: 0; right: 0; top: 38px;
    text-align: center;
    color: var(--red);
    font-weight: 900;
    font-size: 88px;
    line-height: 86px;
    letter-spacing: 1px;
    -webkit-text-stroke: 0;
    text-shadow:
      3px 0 0 var(--white), -3px 0 0 var(--white), 0 3px 0 var(--white), 0 -3px 0 var(--white),
      2px 2px 0 var(--white), -2px -2px 0 var(--white), 2px -2px 0 var(--white), -2px 2px 0 var(--white),
      4px 6px 8px rgba(0,0,0,0.35);
  }
  .headline-line { display: block; }
  .headline-check { position: relative; }
  .check-mark {
    position: absolute; right: -22px; top: -26px;
    width: 78px; height: 72px;
  }
  .check-mark path { fill: none; stroke: #111; stroke-width: 11; stroke-linecap: square; }
  .concerns {
    position: absolute; left: 0; right: 0; top: 243px;
  }
  .concern {
    position: absolute; width: 240px; margin-left: -120px;
    text-align: center;
  }
  .concern-icon {
    width: 164px; height: 164px; margin: 0 auto;
    border-radius: 50%;
    border: 5px solid var(--ring-grey);
    background: var(--white);
    display: flex; align-items: center; justify-content: center;
  }
  .concern-art { width: 96px; height: 112px; border-radius: 46%; }
  .concern-label {
    margin-top: 12px;
    color: var(--red);
    font-weight: 900;
    font-size: 39px;
    line-height: 48px;
  }
  .serve-panel {
    position: absolute; left: 211px; top: 535px;
    width: 766px; height: 132px;
    background: linear-gradient(to bottom, var(--panel-top) 0%, #ededee 45%, var(--panel-bottom) 100%);
    text-align: center;
  }
  .serve-label {
    display: flex; align-items: center; justify-content: center; gap: 10px;
    margin-top: 8px;
    color: var(--ink-grey); font-weight: 800; font-size: 25px; letter-spacing: 0.5px;
  }
  .serve-rule { width: 210px; height: 3px; background: var(--ink-grey); }
  .clinic-name {
    margin-top: 4px;
    color: var(--ink-grey); font-weight: 800; font-size: 50px; line-height: 60px;
  }
  .pet-photo { position: absolute; }
  .pet-photo--cat {
    left: 42px; top: 192px; width: 196px; height: 475px;
    border-radius: 40% 45% 10% 10% / 18% 18% 4% 4%;
    background: linear-gradient(160deg, var(--cat-tone-a) 0%, var(--cat-tone-b) 55%, var(--cat-tone-a) 100%);
  }
  .pet-photo--dog {
    left: 870px; top: 47px; width: 294px; height: 620px;
    border-radius: 45% 45% 12% 12% / 20% 20% 4% 4%;
    background: linear-gradient(170deg, var(--dog-tone-a) 0%, var(--dog-tone-b) 60%, var(--dog-tone-a) 100%);
  }
</style>
</head>
<body>
<main class="banner">
  <div class="pet-photo pet-photo--cat" role="img" aria-label="Photo of a tabby cat walking in from the left, looking up at the headline"></div>
  <div class="pet-photo pet-photo--dog" role="img" aria-label="Photo of a golden-brown dog standing on the right, looking toward the headline"></div>

  <h1 class="headline">
    <span class="headline-line"><span class="headline-check">HEALTH CHECK<svg class="check-mark" viewBox="0 0 78 72" aria-hidden="true"><path d="M8 40 L28 60 L72 8"/></svg></span></span>
    <span class="headline-line">FOR PETS</span>
  </h1>

  <section class="concerns">
    <div class="concern" style="left:390px">
      <div class="concern-icon"><div class="concern-art" style="background:var(--mite-tone)" role="img" aria-label="Illustration of an ear mite"></div></div>
      <p class="concern-label">EAR<br>MITES</p>
    </div>
    <div class="concern" style="left:590px">
      <div class="concern-icon"><div class="concern-art" style="background:var(--pup-tone)" role="img" aria-label="Illustration of a sitting dog with a skin spot"></div></div>
      <p class="concern-label">SKIN<br>HEALTH</p>
    </div>
    <div class="concern" style="left:789px">
      <div class="concern-icon"><div class="concern-art" style="background:var(--tick-tone)" role="img" aria-label="Illustration of a tick bug"></div></div>
      <p class="concern-label">FLEAS<br>&amp; TICKS</p>
    </div>
  </section>

  <footer class="serve-panel">
    <p class="serve-label"><span class="serve-rule"></span>SERVE BY:<span class="serve-rule"></span></p>
    <p class="clinic-name">Paws &amp; Care Vet CLINIC</p>
  </footer>
</main>
</body>
</html>
```